Postcard Design

Sir - I am a delivery company in need of a Postcard of 2500ft Van, a 24ft delivery truck and a 40ft delivery truck. My company has to be on the post card and the vehicles as well.

Reason: Designers must take a look at the home page of my Website@www.drelvanto.com, and come up with a similar design.

Target Market(s)

Manufacturers, Wholesalers and companies that are in need of Cargo vans and Trucks for bulk deliveries.

Industry/Entity Type

It Company

Colors

Designer to choose colors to be used in the design.

```html
<!DOCTYPE html>
<html lang="en">
<head>
<meta charset="utf-8">
<title>Drelvanto Couriers Postcard</title>
<link href="https://fonts.googleapis.com/css2?family=Roboto+Condensed:wght@300;400;700&family=Arimo:wght@400;700&display=swap" rel="stylesheet">
<style>
  :root {
    --navy-deep: #0b1a33;
    --navy: #123461;
    --blue-bright: #1f5fb8;
    --orange: #f39a25;
    --white: #ffffff;
    --strip-grey: #8f959c;
    --ink: #111111;
    --band: rgba(10, 22, 44, 0.55);
  }
  * { margin: 0; padding: 0; box-sizing: border-box; }
  html, body { width: 1200px; height: 930px; overflow: hidden; background: var(--white); }
  .postcard {
    position: relative;
    width: 1200px;
    height: 930px;
    font-family: "Roboto Condensed", "Arial Narrow", sans-serif;
    color: var(--white);
    overflow: hidden;
  }
  .hero {
    position: absolute;
    left: 0; top: 0;
    width: 1200px; height: 755px;
    background:
      radial-gradient(ellipse 620px 460px at 560px 300px, rgba(40, 110, 210, 0.55), transparent 70%),
      radial-gradient(ellipse 500px 400px at 120px 620px, rgba(30, 90, 190, 0.4), transparent 70%),
      linear-gradient(100deg, var(--navy) 0%, #16407a 35%, var(--navy) 65%, var(--navy-deep) 100%);
  }
  .brand {
    position: absolute;
    left: 38px; top: 40px;
    font-weight: 700;
    color: var(--white);
    text-transform: uppercase;
    line-height: 1;
  }
  .brand-name { display: block; font-size: 82px; letter-spacing: -1px; }
  .brand-sub { display: block; font-size: 50px; letter-spacing: 4px; margin: 22px 0 0 130px; }
  .indicia {
    position: absolute;
    left: 1013px; top: 33px;
    width: 146px; height: 148px;
    background: var(--white);
    border: 1.5px solid var(--ink);
    color: var(--ink);
    font-family: "Arimo", Arial, sans-serif;
    font-size: 17.5px;
    line-height: 24px;
    text-align: center;
    padding-top: 11px;
  }
  .indicia strong { font-weight: 700; }
  .features {
    position: absolute;
    left: 45px;
    list-style: none;
    font-weight: 300;
    font-size: 21px;
    line-height: 22.5px;
  }
  .features li { display: flex; align-items: center; gap: 8px; height: 22.5px; }
  .features svg { width: 22px; height: 20px; flex: none; }
  .features-a { top: 272px; }
  .features-b { top: 392px; }
  .features-c { top: 512px; }
  .services-band {
    position: absolute;
    left: 0; top: 624px;
    width: 1200px; height: 48px;
    background: linear-gradient(90deg, var(--band), rgba(10, 22, 44, 0.25) 60%, transparent);
  }
  .services-title {
    position: absolute;
    left: 18px; top: 632px;
    font-weight: 300;
    font-size: 27px;
    text-transform: uppercase;
  }
  .services-list {
    position: absolute;
    left: 18px; top: 678px;
    list-style: none;
    font-weight: 300;
    font-size: 13.5px;
    line-height: 21px;
    text-transform: uppercase;
  }
  .fleet {
    position: absolute;
    left: 0; top: 755px;
    width: 1200px; height: 165px;
    background: var(--white);
  }
  .vehicle {
    position: absolute;
    border-radius: 6px;
  }
  .vehicle-van {
    left: 52px; top: 50px; width: 244px; height: 96px;
    background: linear-gradient(180deg, #f4f5f6, #d9dcdf);
  }
  .vehicle-box-truck {
    left: 332px; top: 38px; width: 314px; height: 110px;
    background: linear-gradient(180deg, #f2f3f4, #d3d6d9);
  }
  .vehicle-semi {
    left: 680px; top: 25px; width: 466px; height: 123px;
    background: linear-gradient(90deg, #3d86d6 0%, #3d86d6 22%, #e9ebed 24%, #d6d9dc 100%);
  }
  .base-strip {
    position: absolute;
    left: 0; top: 920px;
    width: 1200px; height: 10px;
    background: var(--strip-grey);
  }
</style>
</head>
<body>
<main class="postcard">
  <section class="hero">
    <div class="brand">
      <span class="brand-name">Drelvanto</span>
      <span class="brand-sub">Couriers</span>
    </div>

    <div class="indicia">
      PRSRT STD<br>ECRWSS<br>U.S. POSTAGE<br><strong>PAID</strong><br>EDDM RETAIL
    </div>

    <ul class="features features-a">
      <li><svg viewBox="0 0 22 20"><path d="M2 11 L8 17 L20 3" fill="none" stroke="#f39a25" stroke-width="3.5" stroke-linecap="round" stroke-linejoin="round"/></svg>MONEY BACK GUARANTEED IF YOUR PACKAGE IS</li>
      <li><svg viewBox="0 0 22 20"><path d="M2 11 L8 17 L20 3" fill="none" stroke="#f39a25" stroke-width="3.5" stroke-linecap="round" stroke-linejoin="round"/></svg>NOT DELIVERED ON TIME</li>
      <li><svg viewBox="0 0 22 20"><path d="M2 11 L8 17 L20 3" fill="none" stroke="#f39a25" stroke-width="3.5" stroke-linecap="round" stroke-linejoin="round"/></svg>FREE WAITING TIME</li>
      <li><svg viewBox="0 0 22 20"><path d="M2 11 L8 17 L20 3" fill="none" stroke="#f39a25" stroke-width="3.5" stroke-linecap="round" stroke-linejoin="round"/></svg>ALL OUR SERVICES ARE GUARANTEED</li>
    </ul>

    <ul class="features features-b">
      <li><svg viewBox="0 0 22 20"><path d="M2 11 L8 17 L20 3" fill="none" stroke="#f39a25" stroke-width="3.5" stroke-linecap="round" stroke-linejoin="round"/></svg>PICKUP WITHIN 15 TO 30 MINS. OF YOUR CALL OR SOONER</li>
      <li><svg viewBox="0 0 22 20"><path d="M2 11 L8 17 L20 3" fill="none" stroke="#f39a25" stroke-width="3.5" stroke-linecap="round" stroke-linejoin="round"/></svg>FIRST 100LBS. ARE FREE</li>
      <li><svg viewBox="0 0 22 20"><path d="M2 11 L8 17 L20 3" fill="none" stroke="#f39a25" stroke-width="3.5" stroke-linecap="round" stroke-linejoin="round"/></svg>STATE OF THE ART COURIER SOFTWARE SYSTEM</li>
      <li><svg viewBox="0 0 22 20"><path d="M2 11 L8 17 L20 3" fill="none" stroke="#f39a25" stroke-width="3.5" stroke-linecap="round" stroke-linejoin="round"/></svg>ONLINE ORDER ENTRY</li>
    </ul>

    <ul class="features features-c">
      <li><svg viewBox="0 0 22 20"><path d="M2 11 L8 17 L20 3" fill="none" stroke="#f39a25" stroke-width="3.5" stroke-linecap="round" stroke-linejoin="round"/></svg>ONLINE ORDER TRACKING</li>
      <li><svg viewBox="0 0 22 20"><path d="M2 11 L8 17 L20 3" fill="none" stroke="#f39a25" stroke-width="3.5" stroke-linecap="round" stroke-linejoin="round"/></svg>SIGNATURE CAPTURING</li>
      <li><svg viewBox="0 0 22 20"><path d="M2 11 L8 17 L20 3" fill="none" stroke="#f39a25" stroke-width="3.5" stroke-linecap="round" stroke-linejoin="round"/></svg>BE ABLE TO SEE INVOICES ONLINE</li>
      <li><svg viewBox="0 0 22 20"><path d="M2 11 L8 17 L20 3" fill="none" stroke="#f39a25" stroke-width="3.5" stroke-linecap="round" stroke-linejoin="round"/></svg>BE ABLE TO PRINT SHIPPING LABELS</li>
    </ul>

    <div class="services-band"></div>
    <h2 class="services-title">Drelvanto will service the following:</h2>
    <ul class="services-list">
      <li>Hospital &amp; Medical Care – Home deliveries, pharmaceuticals and critical routes.</li>
      <li>Banking &amp; Brokerage – Emergency deliveries, mortgage documents, interoffice routes.</li>
      <li>Legal, administrative and also deliveries associated with manufacturing.</li>
    </ul>
  </section>

  <section class="fleet">
    <div class="vehicle vehicle-van" role="img" aria-label="White cargo van, side view"></div>
    <div class="vehicle vehicle-box-truck" role="img" aria-label="White 24ft box delivery truck, side view"></div>
    <div class="vehicle vehicle-semi" role="img" aria-label="Blue semi truck with 40ft white trailer, side view"></div>
  </section>

  <div class="base-strip"></div>
</main>
</body>
</html>
```